Wordpress Design Project (Brookhollow)

We need a wordpress design for an established auction and real estate company based in New Hampshire. The winning design will incorporate the colors of logo (red and blue) creatively with black or gray in a very professional and clean layout. Client mentions liking the site http://www.pellandbids.example/ as a general idea.

Industry/Entity Type

Real Estate

Requirements
Must have
• Navigation:
1) Home (lorem text)
2) Upcoming Auctions
3) Auction Results
4) Sell or Consign
5) About Us
6) Services
7) FAQ
8) Contact Us

Site will have slideshow, initial image attached.
Sidebar widgets:
- Email sign up form
- Featured Auction (like at http://www.quillmarksales.example) - - - - Video Widget
- Testimonials widget

Footer will have smaller logo, contact info, and 2 association logos (attached)
-
Nice to have
• use of drop-down menu design for 'Services'
1) Appraisals
2) Consulting
Should not have
• please use no gavels in the design

```html
<!DOCTYPE html>
<html lang="en">
<head>
<meta charset="utf-8">
<title>Brookhollow – Auctions</title>
<link href="https://fonts.googleapis.com/css2?family=Arimo:ital,wght@0,400;0,700;1,700&display=swap" rel="stylesheet">
<style>
:root{
  --navy:#0f1a4f;
  --red:#a8161b;
  --red-bright:#c01d22;
  --ink:#1b1b1b;
  --text:#222;
  --line:#d9d9d9;
  --panel:#f1f1f1;
  --dark:#1e1e1e;
  --footer:#1a1a1a;
}
*{box-sizing:border-box;margin:0;padding:0}
html,body{width:881px;height:1200px;overflow:hidden}
body{position:relative;font-family:"Arimo",Arial,sans-serif;color:var(--text);
  background:linear-gradient(#2d2d2d 0,#3a3a3a 60px,#9a9a9a 220px,#e6e6e6 330px,#ececec 360px,#f4f4f4 1130px);}
.topline{position:absolute;top:0;left:0;width:100%;height:3px;background:var(--red)}
.abs{position:absolute}

/* header */
.header{left:75px;top:9px;width:731px;height:341px;background:#fff;box-shadow:0 1px 3px rgba(0,0,0,.3)}
.slide{left:80px;top:14px;width:721px;height:299px;background:linear-gradient(160deg,#6a4a32 0%,#a3937f 30%,#cfc8bd 55%,#8f7f6c 80%,#4a3a2c 100%)}
.brandband{left:66px;top:117px;width:749px;height:80px;background:rgba(255,255,255,.9);box-shadow:0 1px 3px rgba(0,0,0,.25);display:flex;align-items:center;padding-left:30px;gap:10px}
.brandband .mark{width:56px;height:56px;border-radius:50%;background:var(--navy)}
.brandband .name{font-size:24px;color:var(--navy);letter-spacing:.5px}
.nav{left:79px;top:313px;width:723px;height:34px;background:var(--navy);display:flex}
.nav a{color:#fff;text-decoration:none;font-size:11px;display:flex;align-items:center;justify-content:center;border-right:1px solid #26306a;position:relative}
.nav a:last-child{border-right:0}
.nav .on::after{content:"";position:absolute;bottom:4px;left:50%;margin-left:-3px;border:3px solid transparent;border-top-color:#fff}
.dropdown{left:503px;top:347px;width:82px;background:var(--red)}
.dropdown a{display:block;color:#fff;font-size:9px;font-weight:700;padding:5px 6px;text-decoration:none;border-bottom:1px solid #c4484b}
.dropdown a:last-child{border-bottom:0}

/* listings */
.listing{left:76px;width:513px;height:232px;background:var(--panel);border:1px solid #e0e0e0;border-radius:4px}
.listing-head{position:absolute;left:3px;top:1px;width:506px;height:33px;border-radius:4px;background:linear-gradient(#4a4a4a,#111);color:#fff;font-weight:700;font-size:11px;padding-left:15px;display:flex;align-items:center;letter-spacing:.2px}
.thumbbox{position:absolute;left:9px;top:46px;width:117px;height:127px;background:#fff;border:1px solid var(--line);border-radius:3px}
.thumb{position:absolute;left:8px;top:9px;width:100px;height:68px;background:radial-gradient(circle at 30% 50%,#c9a74a 0,#8a6d25 22%,#000 23%),#000}
.details{position:absolute;left:10px;top:91px;width:94px;height:23px;background:linear-gradient(#d1272c,#9a1115);border-radius:3px;color:#fff;font-weight:700;font-size:11px;display:flex;align-items:center;gap:8px;padding-left:12px}
.details svg{width:14px;height:14px}
.info{position:absolute;left:134px;width:368px;background:#fff;border:1px solid var(--line);border-radius:3px;padding:2px 8px;font-size:10px;line-height:12px}
.info-a{top:49px;height:81px}
.info-b{top:137px;height:81px}
.info h3{color:var(--navy);font-size:10.5px;line-height:13px;margin-bottom:4px}
.info .lbl{color:var(--red);font-weight:700;font-size:10.5px;display:block;margin-top:1px}
.info b{font-weight:700}
.info p{margin:0}
.info .addr{margin-top:3px}

/* sidebar */
.widget{left:599px;width:205px;background:linear-gradient(#fff,#ededed);border:1px solid #dcdcdc;border-radius:4px}
.featured{top:369px;height:188px;text-align:center}
.widget h2{font-weight:400;font-size:15px;color:#111;text-align:left}
.featured h2{margin:10px 0 0 18px}
.featured .kind{color:var(--red);font-size:9px;font-weight:700;margin-top:9px}
.featured .pic{margin:5px auto 0;width:124px;height:84px;border:1px solid #555;background:linear-gradient(#8fa2b5,#cfd3d6 45%,#9a9a9a 70%,#555)}
.featured .when{font-size:9px;line-height:12.5px;margin-top:8px;color:#111}
.video{top:575px;height:151px;background:#fff}
.video .screen{position:absolute;left:5px;top:5px;width:194px;height:127px;background:linear-gradient(100deg,#4a1010,#8a6d25 35%,#3a2a22 60%,#7a7670)}
.video .play{position:absolute;left:72px;top:42px;width:48px;height:40px;background:rgba(0,0,0,.55);border-radius:3px}
.video .bar{position:absolute;left:5px;top:132px;width:194px;height:14px;background:#111;color:#fff;font-size:7.5px;display:flex;align-items:center;gap:6px;padding:0 6px}
.video .track{flex:1;height:3px;background:#555}
.email{left:599px;top:743px;width:207px;height:112px;border-radius:4px;background:linear-gradient(#3b3b3b,#0c0c0c);border:1px solid #000}
.email h2{color:#fff;margin:12px 0 0 16px}
.email .field{position:absolute;left:18px;top:39px;width:170px;height:24px;background:#fff;font-size:8.5px;color:#999;padding:7px 8px}
.email .btn{position:absolute;left:101px;top:75px;width:88px;height:24px;background:linear-gradient(#cf2328,#98111a);border-radius:3px;color:#fff;font-weight:700;font-size:12px;display:flex;align-items:center;justify-content:center;letter-spacing:.3px}
.testimonials{top:872px;height:204px}
.testimonials h2{margin:12px 0 0 13px}
.testimonials blockquote{margin:10px 12px 0 16px;font-size:9.6px;line-height:14.6px;color:#222}
.q{font-family:Georgia,serif;font-size:18px;color:#999;line-height:0}
.testimonials cite{display:block;text-align:right;margin:10px 10px 0 0;color:var(--red);font-size:9.5px;font-weight:700;font-style:italic}

/* footer */
.footer{left:0;top:1130px;width:881px;height:70px;background:var(--footer);color:#fff;font-size:9px}
.footer .contact{position:absolute;left:78px;top:20px;line-height:17px}
.footer .fbrand{position:absolute;left:486px;top:19px;width:104px;height:36px;border:1px solid #333;display:flex;align-items:center;gap:5px;padding-left:4px;font-size:11px;color:#fff}
.footer .fbrand i{width:24px;height:24px;border-radius:50%;background:#fff;display:block}
.badge{position:absolute;top:20px;background:#e9e9e9}
</style>
</head>
<body>
<div class="topline"></div>

<div class="abs header"></div>
<div class="abs slide" role="img" aria-label="Photo of a dealer case filled with graded silver and gold coins"></div>
<div class="abs brandband"><span class="mark"></span><span class="name">Brookhollow</span></div>
<nav class="abs nav">
  <a style="width:63px">Home</a>
  <a style="width:131px">Upcoming Auctions</a>
  <a style="width:114px">Auction Results</a>
  <a style="width:110px">Sell or Consign</a>
  <a class="on" style="width:95px">About Us</a>
  <a style="width:79px">Services</a>
  <a style="width:54px">FAQ</a>
  <a style="width:77px">Contact Us</a>
</nav>
<div class="abs dropdown"><a>About Varnholt</a><a>Testimonials</a></div>

<!-- listings -->
<section class="abs listing" style="top:370px">
  <div class="listing-head">HARLOW WELLNESS CENTER IN DUNMORE, NH</div>
  <div class="thumbbox"><div class="thumb" role="img" aria-label="Two gold coins on black"></div>
    <div class="details"><svg viewBox="0 0 14 14"><circle cx="6" cy="6" r="4.5" fill="none" stroke="#fff" stroke-width="1.6"/><path d="M9.5 9.5 13 13" stroke="#fff" stroke-width="2"/></svg>Details</div></div>
  <div class="info info-a"><h3>Marden Tolliver Auctions, LLC NHL 4812 - Everything sold to the high bidder</h3><p>Location:<br>Location 1 - 412 Orchard Ridge Rd<br>Location 2 - 58 Millbrook Ct # 3<br>Dunmore, NH 03299</p></div>
  <div class="info info-b"><span class="lbl">Location:</span><p><b>Began:</b>&nbsp; Friday, May 24, 2013 at 10:06 AM EDT</p><p><b>Ends:</b>&nbsp; Wednesday, June 05, 2013 at 10:00 AM EDT</p><p class="addr">2207 Fenwick Ln. NE<br>Westbury, NH 03288</p></div>
</section>

<section class="abs listing" style="top:620px">
  <div class="listing-head">HARLOW WELLNESS CENTER IN DUNMORE, NH</div>
  <div class="thumbbox"><div class="thumb" role="img" aria-label="Two gold coins on black"></div>
    <div class="details"><svg viewBox="0 0 14 14"><circle cx="6" cy="6" r="4.5" fill="none" stroke="#fff" stroke-width="1.6"/><path d="M9.5 9.5 13 13" stroke="#fff" stroke-width="2"/></svg>Details</div></div>
  <div class="info info-a"><h3>Marden Tolliver Auctions, LLC NHL 4812 - Everything sold to the high bidder</h3><p>Location:<br>Location 1 - 412 Orchard Ridge Rd<br>Location 2 - 58 Millbrook Ct # 3<br>Dunmore, NH 03299</p></div>
  <div class="info info-b"><span class="lbl">Location:</span><p><b>Began:</b>&nbsp; Friday, May 24, 2013 at 10:06 AM EDT</p><p><b>Ends:</b>&nbsp; Wednesday, June 05, 2013 at 10:00 AM EDT</p><p class="addr">2207 Fenwick Ln. NE<br>Westbury, NH 03288</p></div>
</section>

<section class="abs listing" style="top:866px">
  <div class="listing-head">HARLOW WELLNESS CENTER IN DUNMORE, NH</div>
  <div class="thumbbox"><div class="thumb" role="img" aria-label="Two gold coins on black"></div>
    <div class="details"><svg viewBox="0 0 14 14"><circle cx="6" cy="6" r="4.5" fill="none" stroke="#fff" stroke-width="1.6"/><path d="M9.5 9.5 13 13" stroke="#fff" stroke-width="2"/></svg>Details</div></div>
  <div class="info info-a"><h3>Marden Tolliver Auctions, LLC NHL 4812 - Everything sold to the high bidder</h3><p>Location:<br>Location 1 - 412 Orchard Ridge Rd<br>Location 2 - 58 Millbrook Ct # 3<br>Dunmore, NH 03299</p></div>
  <div class="info info-b"><span class="lbl">Location:</span><p><b>Began:</b>&nbsp; Friday, May 24, 2013 at 10:06 AM EDT</p><p><b>Ends:</b>&nbsp; Wednesday, June 05, 2013 at 10:00 AM EDT</p><p class="addr">2207 Fenwick Ln. NE<br>Westbury, NH 03288</p></div>
</section>

<!-- sidebar -->
<aside class="abs widget featured">
  <h2>Featured Auction</h2>
  <div class="kind">AUTOMOBILES - MULTI LOT</div>
  <div class="pic" role="img" aria-label="Silver minivan parked outdoors"></div>
  <div class="when">07/10/13 at 12:00 PM EDT<br>P.O. Box 41175<br>Hallowell, NH 03277</div>
</aside>

<aside class="abs widget video">
  <div class="screen" role="img" aria-label="Video still of an auctioneer beside a large gold coin"></div>
  <svg class="play" viewBox="0 0 48 40"><path d="M18 10 34 20 18 30Z" fill="#fff"/></svg>
  <div class="bar"><span>▶</span><span>00:00</span><span class="track"></span><span>00:00</span><span>◂ıllı</span><span>⤢</span></div>
</aside>

<aside class="abs email">
  <h2>Email sign up</h2>
  <div class="field">Enter Your Email Address...</div>
  <div class="btn">Subscribe</div>
</aside>

<aside class="abs widget testimonials">
  <h2>Client Testimonials</h2>
  <blockquote><span class="q">“</span>simply dummy text of the printing and typesetting industry. Lorem Ipsum has been the industry's took a galley of type and scrambledstandard dummy text ever since the 1500s, when an unknown printer took a galley of type and scrambled it to make took a galley of type and scrambled. <span class="q">”</span></blockquote>
  <cite>By Peter Lanholm...</cite>
</aside>

<footer class="abs footer">
  <div class="contact"><b>Phone:</b> 603- 555-0148, <b>Email:</b> info@brookhollowbids.example<br>Copyright (C) <b>BROOKHOLLOW</b> 2013 - 2014 .&nbsp; All Rights Reserved</div>
  <div class="fbrand"><i></i>Brookhollow</div>
  <div class="badge" style="left:611px;width:34px;height:32px;border-radius:3px"></div>
  <div class="badge" style="left:674px;width:125px;height:31px"></div>
</footer>
</body>
</html>
```